Post it Note design

POST-IT NOTE DESIGN (CONTENT)
Size recommended: 4x6 for handwriting space.
Header (Bold):
Lighting Issue Detected on Your Property
Sub-header:
During our routine night inspection, we noted the following item(s):
Checkbox List:
⬜ Building Lights Out
⬜ Pole Lights Out
⬜ Sign Not Illuminated
⬜ Other ________________________
Action Line:
We can provide a quote or dispatch service right away.
Area for notes
Contact Block (Bold & Centered):
Lumenvale Fixture Inc.
Service@LumenvaleFixture.com
www.LumenvaleFixture.com
877-514-6028
Industry/Entity Type
Electrical lighting
Colors
Designer to choose colors to be used in the design.
Look and feel
Each slider illustrates characteristics of the customer's brand and the style your logo design should communicate.

```html
<!DOCTYPE html>
<html lang="en">
<head>
<meta charset="utf-8">
<title>Lumenvale Fixture Inc. – Lighting Issue Notice</title>
<link href="https://fonts.googleapis.com/css2?family=Poppins:wght@500;600;700;800&display=swap" rel="stylesheet">
<style>
  :root {
    --red: #d0142f;
    --navy: #0a1f8f;
    --white: #ffffff;
    --backdrop: #c4c4c4;
    --sky-top: #5a86c8;
    --sky-bottom: #9ab8e0;
    --vehicle-light: #f1f2f4;
    --vehicle-dark: #b9bec6;
  }
  * { box-sizing: border-box; margin: 0; padding: 0; }
  html, body { width: 1200px; height: 952px; overflow: hidden; }
  body {
    background: var(--backdrop);
    font-family: "Poppins", sans-serif;
    position: relative;
  }
  .note {
    position: absolute;
    top: 164px;
    width: 408px;
    height: 625px;
    background: var(--white);
    overflow: hidden;
  }
  .note--red-footer { left: 144px; }
  .note--navy-footer { left: 635px; }

  .note__header { position: absolute; top: 0; left: 0; width: 100%; height: 94px; }
  .vehicle-photo {
    position: absolute; top: 18px; width: 96px; height: 60px;
    background: linear-gradient(180deg, var(--vehicle-light), var(--vehicle-dark));
    border-radius: 4px;
  }
  .vehicle-photo--truck { left: 12px; }
  .vehicle-photo--van { right: 12px; }
  .brand-name {
    position: absolute; left: 112px; width: 184px; top: 22px;
    text-align: center; color: var(--red);
    font-weight: 800; font-size: 22px; line-height: 1.1;
  }

  .note__title {
    position: absolute; top: 106px; left: 0; width: 100%;
    text-align: center; color: var(--navy);
    font-weight: 700; font-size: 23px; line-height: 28px;
  }

  .band {
    position: absolute; left: 0; width: 100%;
    color: var(--white); text-align: center; font-weight: 700;
    border-top: 2px solid var(--navy); border-bottom: 2px solid var(--navy);
    box-shadow: inset 0 1px 0 var(--white), inset 0 -1px 0 var(--white);
  }
  .band--intro { top: 173px; height: 27px; background: var(--red); font-size: 10.5px; line-height: 23px; font-weight: 600; letter-spacing: -0.1px; }
  .band--action { top: 348px; height: 28px; background: var(--red); font-size: 12px; line-height: 24px; letter-spacing: 0.6px; }

  .checklist { position: absolute; top: 200px; left: 0; width: 214px; height: 148px; list-style: none; }
  .checklist__item {
    position: absolute; left: 23px; height: 16px;
    display: flex; align-items: center; gap: 9px;
    color: var(--navy); font-weight: 600; font-size: 12.5px; white-space: nowrap;
  }
  .checklist__item:nth-child(1) { top: 11px; }
  .checklist__item:nth-child(2) { top: 38px; }
  .checklist__item:nth-child(3) { top: 66px; }
  .checklist__item:nth-child(4) { top: 93px; }
  .checklist__item:nth-child(5) { top: 120px; }
  .checkbox { width: 13px; height: 13px; border: 1.5px solid var(--red); flex: none; background: var(--white); }

  .service-photo {
    position: absolute; top: 200px; left: 214px; width: 194px; height: 148px;
    background: linear-gradient(160deg, var(--sky-top), var(--sky-bottom));
  }

  .notes-area { position: absolute; top: 376px; left: 0; width: 100%; height: 158px; }

  .contact { position: absolute; top: 534px; left: 0; width: 100%; height: 91px; border-top: 2px solid var(--navy); }
  .contact__prompt {
    height: 25px; margin-top: 2px;
    color: var(--white); text-align: center; font-weight: 700; font-size: 12.5px; line-height: 25px;
  }
  .contact__details {
    height: 62px; padding-top: 4px;
    color: var(--white); text-align: center; font-weight: 700; font-size: 13px; line-height: 18px; letter-spacing: 0.6px;
  }
  .contact__phone { letter-spacing: 2.5px; }

  .note--red-footer .contact__prompt { background: var(--navy); }
  .note--red-footer .contact__details { background: var(--red); }
  .note--navy-footer .contact__prompt { background: var(--red); }
  .note--navy-footer .contact__details { background: var(--navy); }
</style>
</head>
<body>

<article class="note note--red-footer">
  <header class="note__header">
    <div class="vehicle-photo vehicle-photo--truck" role="img" aria-label="Photo of a white bucket truck"></div>
    <div class="brand-name">Lumenvale<br>Fixture Inc.</div>
    <div class="vehicle-photo vehicle-photo--van" role="img" aria-label="Photo of a white service van"></div>
  </header>
  <h1 class="note__title">Lighting Issue Detected on<br>Your Property</h1>
  <p class="band band--intro">During our routine night inspection, we noted the following item(s):</p>
  <ul class="checklist">
    <li class="checklist__item"><span class="checkbox"></span>Building Lights Out</li>
    <li class="checklist__item"><span class="checkbox"></span>Pole Lights Out</li>
    <li class="checklist__item"><span class="checkbox"></span>Sign Not Illuminated</li>
    <li class="checklist__item"><span class="checkbox"></span>Canopy Lights</li>
    <li class="checklist__item"><span class="checkbox"></span>Other ___________</li>
  </ul>
  <div class="service-photo" role="img" aria-label="Photo of a technician servicing pole-mounted lights against a blue sky"></div>
  <p class="band band--action">We can provide a quote or dispatch service right away.</p>
  <div class="notes-area"></div>
  <footer class="contact">
    <p class="contact__prompt">Please contact us ASAP or &amp; email to schedule repairs</p>
    <div class="contact__details">
      <p>Service@LumenvaleFixture.com</p>
      <p>www.LumenvaleFixture.com</p>
      <p class="contact__phone">877-514-6028</p>
    </div>
  </footer>
</article>

<article class="note note--navy-footer">
  <header class="note__header">
    <div class="vehicle-photo vehicle-photo--truck" role="img" aria-label="Photo of a white bucket truck"></div>
    <div class="brand-name">Lumenvale<br>Fixture Inc.</div>
    <div class="vehicle-photo vehicle-photo--van" role="img" aria-label="Photo of a white service van"></div>
  </header>
  <h1 class="note__title">Lighting Issue Detected on<br>Your Property</h1>
  <p class="band band--intro">During our routine night inspection, we noted the following item(s):</p>
  <ul class="checklist">
    <li class="checklist__item"><span class="checkbox"></span>Building Lights Out</li>
    <li class="checklist__item"><span class="checkbox"></span>Pole Lights Out</li>
    <li class="checklist__item"><span class="checkbox"></span>Sign Not Illuminated</li>
    <li class="checklist__item"><span class="checkbox"></span>Canopy Lights</li>
    <li class="checklist__item"><span class="checkbox"></span>Other ___________</li>
  </ul>
  <div class="service-photo" role="img" aria-label="Photo of a technician servicing pole-mounted lights against a blue sky"></div>
  <p class="band band--action">We can provide a quote or dispatch service right away.</p>
  <div class="notes-area"></div>
  <footer class="contact">
    <p class="contact__prompt">Please contact us ASAP or &amp; email to schedule repairs</p>
    <div class="contact__details">
      <p>Service@LumenvaleFixture.com</p>
      <p>www.LumenvaleFixture.com</p>
      <p class="contact__phone">877-514-6028</p>
    </div>
  </footer>
</article>

</body>
</html>
```